Event Center Website

We need a new website design for an upscale event center in Reno, Nevada. The building hosts everything from weddings to corporate events to funerals and it competitively more expensive. The overall look and feel is consistent with a Lake Tahoe aesthetic. The current site can be viewed at www.themaplehallevents.com. They are looking for a major upgrade. A sample site they like is www.cliffsidelodgestay.com. We have new photography available (some attached). The site should be very visual. A site map is attached as well for direction on what elements the site should include as well as labels for navigation. I am looking for a home page and sample interior page. Any questions, let me know. Thanks.
Updates

I have added some photography of the center itself for use rather than stock photography. Thanks!

Target Market(s)

Brides, professionals, high-income

Industry/Entity Type

Building

Requirements
Must have
• See site map

```html
<!DOCTYPE html>
<html lang="en">
<head>
<meta charset="utf-8">
<title>Maple Hall – Meet Our Team</title>
<link href="https://fonts.googleapis.com/css2?family=Ubuntu:wght@400;500&display=swap" rel="stylesheet">
<style>
:root{
  --cream:#f5e6c3;
  --cream-glass:rgba(245,230,195,0.9);
  --brown-dark:#4a2c1c;
  --brown-deep:#45230f;
  --brown-mid:#7a4010;
  --orange:#c8701f;
  --accent:#c97a2a;
  --text:#4a3526;
}
*{margin:0;padding:0;box-sizing:border-box}
html,body{width:1200px;height:874px;overflow:hidden}
body{position:relative;font-family:'Ubuntu',sans-serif;color:var(--text);background:var(--cream)}
.hero{position:absolute;left:0;top:0;width:1200px;height:708px;
  background:radial-gradient(ellipse at 50% 25%,#e7a54a 0%,#a8652a 30%,#5a3520 60%,#2e221c 100%)}
.top-links{position:absolute;left:849px;top:0;width:227px;height:52px;background:var(--brown-dark);
  display:flex;align-items:center;justify-content:center;gap:0;color:#f5e6c3;font-size:15px}
.top-links span{padding:0 14px}
.top-links .sep{width:2px;height:26px;background:#f5e6c3;padding:0}
.main-nav{position:absolute;left:100px;top:52px;width:976px;height:58px;background:var(--cream);
  display:flex;align-items:center}
.brand{width:190px;padding-left:12px;font-size:26px;font-weight:500;color:var(--brown-dark)}
.main-nav ul{list-style:none;display:flex;gap:0}
.main-nav li{font-size:14.5px;font-weight:500;color:var(--brown-dark);margin-right:34px;position:relative}
.main-nav li.active::after{content:"";position:absolute;left:-3px;right:-3px;top:29px;height:2px;background:var(--accent)}
.arrow{position:absolute;top:387px;width:46px;height:46px;border-radius:50%;background:rgba(138,66,30,.85)}
.arrow svg{display:block}
.modal{position:absolute;left:212px;top:188px;width:794px;height:405px;background:var(--cream-glass)}
.modal-title{height:49px;border-bottom:1px solid #5a3a28;text-align:center;font-size:25px;font-weight:500;
  color:var(--brown-dark);line-height:50px}
.close{position:absolute;left:763px;top:16px}
.member-head{text-align:center;font-size:26px;font-weight:500;color:var(--brown-dark);margin-top:8px}
.role{color:var(--accent)}
.portrait{position:absolute;left:27px;top:103px;width:235px;height:221px;border:3px solid #6b4a35;
  background:linear-gradient(160deg,#f4f1ec 0%,#e2d6c8 55%,#3b2c24 100%)}
.caption{position:absolute;left:28px;top:335px;font-size:17px;font-weight:500;color:var(--brown-dark)}
.bio{position:absolute;left:283px;top:148px;width:468px;font-size:13.7px;line-height:22.3px;text-align:justify;color:var(--text)}
.scroll{position:absolute;left:775px;top:61px;width:7px;height:313px;border-radius:4px;background:var(--brown-dark)}
.scroll i{position:absolute;left:2px;top:39px;width:3px;height:39px;background:var(--orange)}
.signup{position:absolute;left:131px;top:747px;width:340px;height:60px;display:flex;border-radius:3px;overflow:hidden}
.signup .field{flex:1;background:var(--brown-mid);color:#f5e6c3;font-size:15px;display:flex;align-items:center;padding-left:9px;justify-content:space-between;padding-right:10px}
.signup .send{width:56px;background:var(--orange);color:#f5e6c3;font-size:15px;display:flex;align-items:center;justify-content:center}
.contact{position:absolute;left:495px;top:748px;width:362px;height:58px;background:var(--brown-deep);border-radius:3px;
  display:flex;color:#f5e6c3;font-size:13px;line-height:23px}
.contact .addr{width:150px;padding:8px 0 0 11px;border-right:1px solid #8a5a3a}
.contact .reach{padding:6px 0 0 10px}
.contact em{font-style:normal;color:var(--orange);margin-right:6px}
.social{position:absolute;left:887px;top:748px;width:189px;height:60px;background:var(--brown-deep);border-radius:3px;
  display:flex;align-items:center;justify-content:center;gap:11px}
.social span{width:29px;height:29px;background:#c8701f;border-radius:2px}
.footer-nav{position:absolute;left:0;top:835px;width:1200px;display:flex;justify-content:center;gap:28px;
  font-size:14px;color:var(--brown-dark);list-style:none}
</style>
</head>
<body>
<div class="hero" role="img" aria-label="Interior of the event hall with chandelier, draped ceiling fabric, rows of covered chairs and a red aisle runner"></div>

<div class="top-links"><span>FAQ</span><span class="sep"></span><span>TESTIMONIAL</span></div>

<nav class="main-nav">
  <div class="brand">Maple Hall</div>
  <ul>
    <li class="active">ABOUT US</li><li>GALLERY</li><li>WEDDING</li><li>MEETINGS</li><li>OTHER EVENTS</li><li>CATERING</li><li>MENUS</li>
  </ul>
</nav>

<div class="arrow" style="left:22px"><svg width="46" height="46" viewBox="0 0 46 46"><path d="M23 15l-8 8 8 8M30 15l-8 8 8 8" fill="none" stroke="#fff" stroke-width="2.5"/></svg></div>
<div class="arrow" style="left:1129px"><svg width="46" height="46" viewBox="0 0 46 46"><path d="M16 15l8 8-8 8M23 15l8 8-8 8" fill="none" stroke="#fff" stroke-width="2.5"/></svg></div>

<section class="modal">
  <h1 class="modal-title">MEET OUR TEAM</h1>
  <svg class="close" width="22" height="22" viewBox="0 0 22 22"><circle cx="11" cy="11" r="11" fill="#3a2a20"/><path d="M7 7l8 8M15 7l-8 8" stroke="#fff" stroke-width="2.5"/></svg>
  <h2 class="member-head">Dana, <span class="role">Operations Manager</span></h2>
  <div class="portrait" role="img" aria-label="Portrait photo of the operations manager"></div>
  <p class="caption">Dana, <span class="role">Operations Manager</span></p>
  <p class="bio">Dana moved to Reno when she was in the Fifth grade and attended schools in the Reno/Sparks area. She was a property and equipment manager before coming to Maple Hall. Dana has been with Maple Hall since it opened its doors in 2009. Dana is responsible for accounts payable, managing pay-roll and is our Human Resources guru. Her main responsibility is to make sure that Lena doesn’t forget to cross her t’s and dot her i’s. She works with clients on a daily basis to help make their vision come to fruition. Dana and her husband are very busy shuttling and attending sporting events for three amazing boys.</p>
  <div class="scroll"><i></i></div>
</section>

<form class="signup">
  <div class="field">ENTER YOUR EMAIL
    <svg width="32" height="30" viewBox="0 0 32 30"><path d="M2 13l14-11 14 11v15H2z" fill="#fff"/><path d="M2 13l14 9 14-9" fill="none" stroke="#7a4010" stroke-width="1.5"/><circle cx="16" cy="9" r="3" fill="none" stroke="#7a4010" stroke-width="1.3"/></svg>
  </div>
  <div class="send">SEND</div>
</form>

<div class="contact">
  <div class="addr">420 Ridgeview Lane<br>Reno, NV 89502</div>
  <div class="reach"><em>Phone:</em>775-555-0142<br><em>Email:</em>info@themaplehallevents.com</div>
</div>

<div class="social" aria-label="Social links"><span></span><span></span><span></span><span></span></div>

<ul class="footer-nav">
  <li>ABOUT US</li><li>GALLERY</li><li>WEDDING</li><li>MEETINGS</li><li>OTHER EVENTS</li><li>CATERING</li><li>MENUS</li>
</ul>
</body>
</html>
```